3x6 ft. Vertical Banner for Summer Camp Info Fair

We are a summer camp and will be presenting our camp at a camp fair on Saturday, March 5th (1 week from now). The sign needs to be 3x6 ft vertical.

We need a single display board that really communicates what our program is. We will include our logo, content and photos. Please refer to our website for a feel of our program and feel free to use any of the content on there (photos, content ideas, etc. ) http://brightmeadowclub.example/summer-program/

Target Market(s)

White, Asian, Indian parents who are in their 30s -50s who have school aged children (ages 4-11) who are mid-upper middle class and both parents are working. They are busy, stressed, guilty parents who value education, safety, fun and convenience.

Industry/Entity Type

Summer Camp/Child Care

Colors

Designer to choose colors to be used in the design.

Requirements
Must have
• Our Summer Program logo AND our business logo (apple), our 3 uniques (Fun, Flexible, Family), Colorful and fun-looking. Plenty of pictures. Some basic business info including: Serving Westford and beyond since 1997. Ages: 5-11. 47 Harrow Ln. Westford, MA.
Nice to have
• Clip art-styled Pine Trees
Should not have
• Pictures of people or kids wearing masks

```html
<!DOCTYPE html>
<html lang="en">
<head>
<meta charset="UTF-8">
<title>Bright Meadow Club – Summer Program Banner</title>
<link href="https://fonts.googleapis.com/css2?family=Baloo+2:wght@600;800&family=Luckiest+Guy&display=swap" rel="stylesheet">
<style>
  :root {
    --bg: #e4e4e4;
    --sky-top: #cfeaf5;
    --sky-mid: #f4fbfe;
    --green: #3fb54a;
    --red: #e3262b;
    --blue: #1a37b8;
    --white: #ffffff;
    --ink: #1d1d1d;
    --sun: #f7c21b;
  }
  * { box-sizing: border-box; margin: 0; padding: 0; }
  html, body { width: 1200px; height: 960px; overflow: hidden; }
  body { background: var(--bg); position: relative; font-family: "Baloo 2", sans-serif; }

  .banner {
    position: absolute; left: 375px; top: 30px;
    width: 450px; height: 900px; overflow: hidden;
    box-shadow: 0 10px 30px rgba(0,0,0,.25);
  }
  .banner-bg { position: absolute; inset: 0; }

  .brand {
    position: absolute; transform: translate(-50%, -50%);
    display: flex; flex-direction: column; align-items: center; gap: 6px;
    text-align: center;
  }
  .brand-mark { width: 70px; height: 70px; border-radius: 50%; }
  .brand-mark.sun { background: var(--sun); }
  .brand-mark.apple { background: var(--red); }
  .brand-name { font-family: "Baloo 2", sans-serif; font-weight: 800; font-size: 19px; line-height: 1; color: var(--ink); width: 150px; }
  .brand.summer { left: 135px; top: 113px; }
  .brand.club { left: 320px; top: 108px; }

  .unique {
    position: absolute; z-index: 2;
    transform: translate(-50%, -50%) rotate(-8deg);
    font-family: "Luckiest Guy", "Baloo 2", sans-serif;
    font-weight: 800; line-height: 1; white-space: nowrap; letter-spacing: 0.5px;
  }
  .unique.fun { left: 114px; top: 232px; font-size: 40px; color: var(--red); }
  .unique.flexible { left: 124px; top: 278px; font-size: 34px; color: var(--green); }
  .unique.family { left: 132px; top: 316px; font-size: 38px; color: var(--blue); }

  .photo {
    position: absolute; z-index: 1;
    border: 6px solid var(--white);
    box-shadow: 0 3px 8px rgba(0,0,0,.3);
  }
  .photo.red-frame { border-color: var(--red); }
  .photo.green-frame { border-color: var(--green); }
  .photo.picnic { left: 318px; top: 285px; width: 180px; height: 130px; transform: translate(-50%,-50%) rotate(10deg); background: linear-gradient(160deg, #6e9b4a, #c98a6e 55%, #3b5f8a); }
  .photo.treats { left: 139px; top: 422px; width: 178px; height: 130px; transform: translate(-50%,-50%) rotate(-12deg); background: linear-gradient(150deg, #5e7d3e, #e8b0a8 50%, #f2a6c6); }
  .photo.hoops { left: 320px; top: 440px; width: 180px; height: 130px; transform: translate(-50%,-50%) rotate(12deg); background: linear-gradient(140deg, #8f8f8a, #b8a9c9 45%, #d9c86a); }
  .photo.beach { left: 135px; top: 578px; width: 196px; height: 140px; transform: translate(-50%,-50%) rotate(-12deg); background: linear-gradient(180deg, #9ec6e6 0%, #5b8fb8 35%, #d6c3a0 60%, #b59f80 100%); }
  .photo.pond { left: 335px; top: 594px; width: 180px; height: 136px; transform: translate(-50%,-50%) rotate(12deg); background: linear-gradient(170deg, #4f6f3c, #6b8c58 45%, #5c8a3a); }

  .info { position: absolute; left: 0; width: 450px; text-align: center; color: var(--white); }
  .serving { top: 662px; font-size: 62px; font-weight: 800; line-height: 1; }
  .reach { top: 722px; font-size: 28px; font-weight: 800; line-height: 1; }
  .rule { position: absolute; left: 75px; width: 300px; height: 1.5px; background: var(--white); }
  .rule.upper { top: 762px; }
  .rule.lower { top: 794px; }
  .since { top: 767px; font-size: 21px; font-weight: 800; letter-spacing: 5px; line-height: 1.2; }
  .ages { top: 798px; font-size: 48px; font-weight: 800; line-height: 1; }
  .address { top: 850px; font-size: 18px; font-weight: 600; line-height: 1; }
</style>
</head>
<body>
  <main class="banner">
    <svg class="banner-bg" width="450" height="900" viewBox="0 0 450 900" aria-hidden="true">
      <defs>
        <radialGradient id="sky" cx="0.5" cy="0.3" r="0.8">
          <stop offset="0" stop-color="#f4fbfe"/>
          <stop offset="1" stop-color="#cfeaf5"/>
        </radialGradient>
      </defs>
      <rect width="450" height="900" fill="url(#sky)"/>
      <polygon points="0,0 150,0 0,46" fill="#3fb54a"/>
      <polygon points="0,431 450,298 450,900 0,900" fill="#3fb54a"/>
      <polygon points="0,670 450,535 450,900 0,900" fill="#e3262b"/>
    </svg>

    <div class="brand summer">
      <span class="brand-mark sun"></span>
      <span class="brand-name">Bright Meadow Club Summer</span>
    </div>
    <div class="brand club">
      <span class="brand-mark apple"></span>
      <span class="brand-name">Bright Meadow Club</span>
    </div>

    <div class="photo red-frame picnic" role="img" aria-label="Photo of campers gathered on the grass at a picnic"></div>
    <div class="photo hoops" role="img" aria-label="Photo of children playing inside colourful hula hoops"></div>
    <div class="photo red-frame treats" role="img" aria-label="Photo of children enjoying cotton candy outdoors"></div>
    <div class="photo green-frame pond" role="img" aria-label="Photo of campers exploring a lily pond"></div>
    <div class="photo beach" role="img" aria-label="Photo of campers posing together on a lake beach"></div>

    <div class="unique fun">FUN</div>
    <div class="unique flexible">FLEXIBLE</div>
    <div class="unique family">FAMILY</div>

    <div class="info serving">Serving</div>
    <div class="info reach">Westford and beyond</div>
    <span class="rule upper"></span>
    <div class="info since">SINCE 1997</div>
    <span class="rule lower"></span>
    <div class="info ages">AGES: 5-11</div>
    <div class="info address">47 Harrow Ln. Westford, MA</div>
  </main>
</body>
</html>
```